Brightwell Counseling Business Card Design Project

I am starting a new business that provides counseling and coaching services to individuals and couples. These individuals are people looking to "transform" or grow in the personal lives. The design should convey trust, intimacy, hope, growth. It should be professional, elegant.
Contact information
Name: Dana R. Holcomb
Title: Counselor and Life Coach
Slogan: Bringing Hope. Transforming Lives.
address: 40917 Ridgecrest Road, Suite 300
Plymouth, MN 55392
Phone: 763-804-7719
Email: dana@brightwell-kx.example
website: www.brightwell-kx.example
Back side of card should have bullets:
Individual counseling
Relationship counseling
Life Coaching for Teens and Adults
Group Workshops

```html
<!DOCTYPE html>
<html lang="en">
<head>
<meta charset="utf-8">
<title>Brightwell Counseling – Business Card</title>
<link rel="stylesheet" href="https://fonts.googleapis.com/css2?family=Cinzel:wght@500&family=Open+Sans:ital,wght@0,400;0,700;1,400&display=swap">
<style>
  :root {
    --backdrop: #e9e7e4;
    --card: #ffffff;
    --brand-blue: #1f6a9a;
    --name-blue: #1f4d78;
    --ink: #2b2b2b;
    --muted: #5a5a5a;
    --mark-blue: #2a6f9e;
    --card-shadow: rgba(0, 0, 0, 0.18);
  }
  * { box-sizing: border-box; margin: 0; padding: 0; }
  html, body {
    width: 1200px;
    height: 475px;
    overflow: hidden;
    background: var(--backdrop);
  }
  .canvas {
    position: relative;
    width: 1200px;
    height: 475px;
  }
  .card {
    position: absolute;
    width: 523px;
    height: 298px;
    background: var(--card);
    box-shadow: 0 3px 10px var(--card-shadow);
  }
  .card--front { left: 57px; top: 88px; }
  .card--back  { left: 627px; top: 91px; }

  .brand-mark {
    position: absolute;
    border-radius: 50%;
    background: var(--mark-blue);
  }
  .card--front .brand-mark {
    left: 48px; top: 80px;
    width: 140px; height: 140px;
  }
  .brand-name {
    position: absolute;
    font-family: "Cinzel", serif;
    font-weight: 500;
    color: var(--brand-blue);
    white-space: nowrap;
    letter-spacing: 0.5px;
  }
  .card--front .brand-name {
    right: 28px; top: 52px;
    font-size: 21px;
  }

  .contact {
    position: absolute;
    right: 28px;
    top: 128px;
    text-align: right;
    font-family: "Open Sans", sans-serif;
    color: var(--ink);
  }
  .contact__name {
    font-weight: 700;
    font-size: 16px;
    line-height: 22px;
    color: var(--name-blue);
  }
  .contact__title {
    font-size: 12px;
    line-height: 17px;
    color: var(--muted);
    margin-bottom: 8px;
  }
  .contact__line {
    display: flex;
    justify-content: flex-end;
    align-items: center;
    gap: 5px;
    font-size: 13.5px;
    line-height: 19px;
  }
  .contact__icon {
    width: 11px;
    height: 11px;
    fill: var(--name-blue);
  }
  .contact__address {
    margin-top: 10px;
    font-size: 14px;
    line-height: 20px;
  }

  .card--back .brand-lockup {
    position: absolute;
    left: 0; right: 0; top: 52px;
    display: flex;
    justify-content: center;
    align-items: center;
    gap: 12px;
  }
  .card--back .brand-mark {
    position: static;
    width: 40px; height: 40px;
  }
  .card--back .brand-name {
    position: static;
    font-size: 24px;
  }
  .slogan {
    position: absolute;
    left: 0; right: 0; top: 106px;
    text-align: center;
    font-family: "Open Sans", sans-serif;
    font-style: italic;
    font-size: 13px;
    color: var(--name-blue);
  }
  .services {
    position: absolute;
    left: 60px; right: 40px; top: 146px;
    list-style: none;
    display: grid;
    grid-template-columns: 1fr 1fr;
    row-gap: 8px;
    column-gap: 16px;
    font-family: "Open Sans", sans-serif;
    font-size: 12px;
    line-height: 16px;
    color: var(--ink);
  }
  .services__item {
    display: flex;
    align-items: center;
    gap: 7px;
    white-space: nowrap;
  }
  .services__item::before {
    content: "";
    width: 6px;
    height: 6px;
    border-radius: 50%;
    background: var(--brand-blue);
    flex: none;
  }
  .card--back .website {
    position: absolute;
    left: 0; right: 0; top: 240px;
    text-align: center;
    font-family: "Open Sans", sans-serif;
    font-size: 14px;
    letter-spacing: 1.4px;
    color: var(--ink);
  }
</style>
</head>
<body>
<main class="canvas">

  <section class="card card--front" aria-label="Card front">
    <span class="brand-mark" aria-hidden="true"></span>
    <h1 class="brand-name">Brightwell Counseling</h1>

    <div class="contact">
      <p class="contact__name">Dana R. Holcomb</p>
      <p class="contact__title">Counselor and Life Coach</p>
      <p class="contact__line">
        <svg class="contact__icon" viewBox="0 0 12 12" aria-hidden="true"><path d="M2.5 1h2l1 3-1.5 1c.6 1.3 1.7 2.4 3 3l1-1.5 3 1v2c0 .6-.4 1-1 1C5.3 10.5 1.5 6.7 1.5 2c0-.6.4-1 1-1z"/></svg>
        763-804-7719
      </p>
      <p class="contact__line">
        <svg class="contact__icon" viewBox="0 0 12 12" aria-hidden="true"><path d="M1 3h10v7H1z M1 3l5 4 5-4" stroke="#fff" stroke-width="0.8"/></svg>
        dana@brightwell-kx.example
      </p>
      <p class="contact__line">
        <svg class="contact__icon" viewBox="0 0 12 12" aria-hidden="true"><circle cx="6" cy="6" r="5"/><path d="M1 6h10M6 1c-2.5 3-2.5 7 0 10M6 1c2.5 3 2.5 7 0 10" stroke="#fff" stroke-width="0.7" fill="none"/></svg>
        www.brightwell-kx.example
      </p>
      <p class="contact__address">40917 Ridgecrest Road, Suite 300<br>Plymouth, MN 55392</p>
    </div>
  </section>

  <section class="card card--back" aria-label="Card back">
    <div class="brand-lockup">
      <span class="brand-mark" aria-hidden="true"></span>
      <h2 class="brand-name">Brightwell Counseling</h2>
    </div>
    <p class="slogan">Bringing Hope. Transforming Lives.</p>
    <ul class="services">
      <li class="services__item">Individual counseling</li>
      <li class="services__item">Relationship counseling</li>
      <li class="services__item">Life Coaching for Teens and Adults</li>
      <li class="services__item">Group Workshops</li>
    </ul>
    <p class="website">www.brightwell-kx.example</p>
  </section>

</main>
</body>
</html>
```